Laser Tattoo Removal Business Cards

We are looking for a professional business card design for a laser tattoo removal business. Ideally looking for a black business card design. The name of the business is Brightline Tattoo Removal. We place our cards at local tattoo shops so we ideally are looking for something trendy/edgy to draw both male and female clientele in.

Target Market(s)

Male/Female ages 18-60

Contact Information for Business Card

black background ideally.. hoping to stay within greys, whites and black

Font styles to use
Serif
Sans Serif

Colors
121212
a9a9a9
5c5c5c
f5f5f5
ffffff
7f7f7f
606060
848484
9d9d9d

Requirements
Must have
• Employee Info:
• Melissa Thornbury
• Chief Executive Offer
• m: 919.537.2846
• w: 919.362.4178
• f: 919.685.3907
• mthornbury@brightlinetattooremoval.example
• Address:
• 4615 Oakmere Pkwy, Suite 210
• Raleigh, NC 27654
• Website:
• www.brightlinetattooremoval.example
Nice to have
• Myabe business name on back or logo on back and employee info on the front

```html
<!DOCTYPE html>
<html lang="en">
<head>
<meta charset="utf-8">
<title>Brightline Tattoo Removal – Business Cards</title>
<link rel="stylesheet" href="https://fonts.googleapis.com/css2?family=Roboto:wght@400;500&family=Roboto+Condensed:wght@500&display=swap">
<style>
  :root {
    --ink: #121212;
    --band: #262626;
    --paper: #f5f5f5;
    --white: #ffffff;
    --grey-light: #a9a9a9;
    --grey-mid: #848484;
    --grey-dark: #5c5c5c;
    --stage: #d6d6d6;
  }
  * { margin: 0; padding: 0; box-sizing: border-box; }
  html, body { width: 1200px; height: 960px; overflow: hidden; }
  body {
    position: relative;
    background: var(--stage);
    font-family: "Roboto", Arial, sans-serif;
  }
  .card {
    position: absolute;
    width: 600px;
    height: 343px;
    overflow: hidden;
  }
  /* Front */
  .card--front { left: 314px; top: 113px; background: var(--paper); }
  .front-brand {
    position: absolute;
    right: 40px;
    top: 52px;
    width: 230px;
    text-align: center;
    color: var(--ink);
    font-weight: 500;
  }
  .front-brand .brand-name { font-size: 34px; letter-spacing: 2px; line-height: 1; }
  .front-brand .brand-sub { margin-top: 14px; font-size: 14px; letter-spacing: 3px; }
  .holder { position: absolute; left: 31px; top: 160px; }
  .holder-name {
    font-family: "Roboto Condensed", Arial, sans-serif;
    font-weight: 500;
    font-size: 21px;
    color: var(--ink);
    line-height: 1;
  }
  .holder-title { font-size: 14px; color: var(--grey-mid); margin-top: 4px; }
  .contact-band {
    position: absolute;
    left: 0; top: 203px;
    width: 100%; height: 115px;
    background: var(--band);
    color: var(--white);
    font-size: 13px;
  }
  .contact-list { position: absolute; left: 31px; top: 20px; list-style: none; }
  .contact-list li { display: flex; align-items: center; height: 19.5px; white-space: nowrap; }
  .contact-list svg { width: 12px; height: 12px; margin-right: 10px; fill: var(--white); flex: none; }
  .address {
    position: absolute; right: 32px; top: 26px;
    text-align: right; font-style: normal; line-height: 18.5px; white-space: nowrap;
  }
  /* Back */
  .card--back { left: 311px; top: 472px; background: var(--ink); }
  .back-brand {
    position: absolute; left: 0; top: 110px; width: 100%;
    text-align: center; color: var(--white); font-weight: 500;
  }
  .back-brand .brand-name { font-size: 46px; letter-spacing: 3px; line-height: 1; }
  .back-brand .brand-sub { margin-top: 24px; font-size: 18px; letter-spacing: 4px; }
  .web-band {
    position: absolute; left: 0; top: 289px;
    width: 100%; height: 26px;
    background: var(--white);
    color: var(--ink);
    font-size: 14px; letter-spacing: 2.4px;
    text-align: center; line-height: 26px;
  }
</style>
</head>
<body>
  <section class="card card--front">
    <div class="front-brand">
      <div class="brand-name">BRIGHTLINE</div>
      <div class="brand-sub">— TATTOO REMOVAL —</div>
    </div>
    <div class="holder">
      <div class="holder-name">MELISSA THORNBURY</div>
      <div class="holder-title">Chief Executive Offer</div>
    </div>
    <div class="contact-band">
      <ul class="contact-list">
        <li><svg viewBox="0 0 24 24"><path d="M6.6 10.8a15 15 0 0 0 6.6 6.6l2.2-2.2c.3-.3.7-.4 1-.2 1.1.4 2.3.6 3.6.6.6 0 1 .4 1 1V20c0 .6-.4 1-1 1A17 17 0 0 1 3 4c0-.6.4-1 1-1h3.5c.6 0 1 .4 1 1 0 1.3.2 2.5.6 3.6.1.3 0 .7-.2 1z"/></svg>919.362.4178</li>
        <li><svg viewBox="0 0 24 24"><path d="M7 1h10a2 2 0 0 1 2 2v18a2 2 0 0 1-2 2H7a2 2 0 0 1-2-2V3a2 2 0 0 1 2-2zm0 3v14h10V4z"/></svg>919.537.2846</li>
        <li><svg viewBox="0 0 24 24"><path d="M6 2h12v5H6zM3 8h18a1 1 0 0 1 1 1v8h-4v5H6v-5H2V9a1 1 0 0 1 1-1zm5 8v4h8v-4z"/></svg>919.685.3907</li>
        <li><svg viewBox="0 0 24 24"><path d="M2 5h20v14H2zm2 2v1l8 5 8-5V7l-8 5z"/></svg>mthornbury@brightlinetattooremoval.example</li>
      </ul>
      <address class="address">
        4615 Oakmere Pkwy<br>
        Suite 210<br>
        Raleigh, NC 27654<br>
        www.brightlinetattooremoval.example
      </address>
    </div>
  </section>

  <section class="card card--back">
    <div class="back-brand">
      <div class="brand-name">BRIGHTLINE</div>
      <div class="brand-sub">— TATTOO REMOVAL —</div>
    </div>
    <div class="web-band">www.brightlinetattooremoval.example</div>
  </section>
</body>
</html>
```